American cannabis tech company business card design

Pavrel.com is seeking a modern, professional, and brand-aligned business card that represents our company and its core values: Mission, Story, Values, and Impact. As an innovative cannabis company, we want a business card that is not only visually appealing but also serves as a representation of who we are and what we stand for.

Project Scope: Design a double-sided business card that integrates our brand identity and core values. Incorporate our key brand elements, ensuring a sleek and contemporary aesthetic. Visually reflect our core values (Mission, Story, Values, Impact) in a way that is engaging yet professional.

Target Market(s)

Vendors, third parties,

Contact Information for Business Card

Contact details (name, title, email, phone, website, etc.)

Font styles to use
Other font styles liked:
• Caslon, Centra

Colors

Designer to choose colors to be used in the design.

Requirements
Must have
• Pavrel.com logo and branding A creative yet clean way to integrate our core values (Mission, Story, Values, Impact) Modern typography and a well-structured layout
Nice to have
• forest green, grey, white, black
Should not have
• references to marijuana, leafs, plants, or related product

```html
<!DOCTYPE html>
<html lang="en">
<head>
<meta charset="utf-8">
<title>Pavrel.com – Round Business Card</title>
<link href="https://fonts.googleapis.com/css2?family=Poppins:wght@400;500;600;700&display=swap" rel="stylesheet">
<style>
  :root {
    --backdrop: #5c5c5c;
    --card-front: #ececec;
    --card-back: #ffffff;
    --forest: #183a1f;
    --forest-text: #1f2f22;
  }
  * { margin: 0; padding: 0; box-sizing: border-box; }
  html, body {
    width: 1200px;
    height: 900px;
    overflow: hidden;
    background: var(--backdrop);
    font-family: "Poppins", sans-serif;
  }
  .canvas {
    position: relative;
    width: 1200px;
    height: 900px;
  }
  .card {
    position: absolute;
    top: 235px;
    width: 414px;
    height: 414px;
    border-radius: 50%;
    display: flex;
    flex-direction: column;
    align-items: center;
    justify-content: center;
    text-align: center;
  }
  .card--front {
    left: 184px;
    background: var(--card-front);
  }
  .card--back {
    left: 623px;
    background: var(--card-back);
    color: var(--forest-text);
    padding-top: 18px;
  }
  .brand-name {
    font-weight: 700;
    font-size: 74px;
    letter-spacing: 1px;
    color: var(--forest);
    line-height: 1;
    margin-top: 40px;
  }
  .core-values {
    margin-top: 18px;
    font-weight: 500;
    font-size: 12px;
    letter-spacing: 2px;
    color: var(--forest);
  }
  .contact-name {
    font-weight: 600;
    font-size: 25px;
    letter-spacing: 0.5px;
    color: var(--forest);
    line-height: 1.1;
  }
  .contact-title {
    font-size: 18.5px;
    line-height: 1.3;
    margin-bottom: 20px;
  }
  .contact-lines,
  .contact-address {
    font-size: 19px;
    line-height: 24px;
  }
  .contact-lines { margin-bottom: 19px; }
</style>
</head>
<body>
  <main class="canvas">
    <section class="card card--front" aria-label="Card front">
      <div class="brand-name">PAVREL</div>
      <div class="core-values">MISSION · STORY · VALUES · IMPACT</div>
    </section>
    <section class="card card--back" aria-label="Card back">
      <div class="contact-name">DANIEL REYES</div>
      <div class="contact-title">Managing Director</div>
      <div class="contact-lines">
        <div class="contact-phone">044-210 987 654</div>
        <div class="contact-email">info@pavrel.com</div>
        <div class="contact-web">www.pavrel.com</div>
      </div>
      <div class="contact-address">
        421, Address line name<br>goes here 45452,Country
      </div>
    </section>
  </main>
</body>
</html>
```